Medical VIP club - small design

Please read the specs in a design brief attached. Also we don't have logo in a Vector format and attaching the only version we have.

Club

```html
<!DOCTYPE html>
<html lang="en">
<head>
<meta charset="utf-8">
<title>Velmora – VIP Club</title>
<link rel="stylesheet" href="https://fonts.googleapis.com/css2?family=Arimo:wght@400;700&display=swap">
<style>
  :root {
    --page-bg: #5d4d36;
    --band: #efe3cc;
    --header-light: #f3ede0;
    --header-mid: #cdbf9f;
    --header-dark: #8a7a5b;
    --tab-top: #c4b596;
    --tab-bottom: #6f5f45;
    --tab-vip-top: #d6d27a;
    --tab-vip-bottom: #8f8c37;
    --tab-reg-top: #f5cf46;
    --tab-reg-bottom: #b28c13;
    --panel-bar-top: #92876a;
    --panel-bar-bottom: #675b41;
    --panel-bg: #ffffff;
    --text: #4a4a4a;
    --rule: #e4e0d8;
    --brand: #5a4a2e;
    --white: #ffffff;
  }
  * { box-sizing: border-box; margin: 0; padding: 0; }
  html, body { width: 1200px; height: 874px; overflow: hidden; }
  body {
    position: relative;
    background: var(--page-bg);
    font-family: "Arimo", Arial, sans-serif;
  }
  .nav-band {
    position: absolute; left: 0; top: 240px; width: 1200px; height: 40px;
    background: linear-gradient(var(--band), #d9c9a8);
  }
  .site-header {
    position: absolute; left: 24px; top: 10px; width: 1158px; height: 188px;
    border-radius: 14px; overflow: hidden;
    border: 1px solid #e9dfc8;
    background: linear-gradient(180deg, var(--header-light) 0%, var(--header-mid) 55%, var(--header-dark) 100%);
  }
  .header-scene {
    position: absolute; left: 447px; top: 0; width: 711px; height: 188px;
    background: linear-gradient(100deg, rgba(205,191,159,0) 0%, #4f8fa0 14%, #3b7f95 40%, #9a8f6e 62%, #5f7f4a 80%, #8c8d80 100%);
  }
  .brand {
    position: absolute; left: 40px; top: 70px;
    display: flex; align-items: center; gap: 14px;
    font-size: 56px; font-weight: 700; color: var(--brand); letter-spacing: 1px;
  }
  .brand-dot { width: 34px; height: 34px; border-radius: 50%; background: var(--brand); }
  .phone-badge {
    position: absolute; left: 766px; top: 43px; width: 104px; height: 104px; border-radius: 50%;
    background: radial-gradient(circle at 40% 30%, #d7b56a, #8a6223 75%);
    border: 3px solid #f2e3c0;
    display: flex; align-items: center; justify-content: center;
  }
  .phone-number {
    position: absolute; left: 888px; top: 74px;
    font-size: 45px; font-weight: 700; color: var(--white);
    text-shadow: 0 0 3px #3a2e1c, 0 2px 4px #3a2e1c;
  }
  .main-nav { position: absolute; left: 24px; top: 207px; display: flex; gap: 4px; }
  .nav-tab {
    width: 190px; height: 72px; border-radius: 12px 12px 0 0;
    background: linear-gradient(var(--tab-top), var(--tab-bottom));
    color: var(--white); font-size: 20px;
    display: flex; align-items: center; justify-content: center;
    text-shadow: 0 1px 1px rgba(0,0,0,.35);
  }
  .nav-tab--vip { background: linear-gradient(var(--tab-vip-top), var(--tab-vip-bottom)); }
  .nav-tab--register { background: linear-gradient(var(--tab-reg-top), var(--tab-reg-bottom)); }
  .content-panel {
    position: absolute; left: 20px; top: 289px; width: 1167px; height: 485px;
    background: var(--panel-bg); border-radius: 12px; overflow: hidden;
    border: 1px solid #d9d2c0;
  }
  .panel-title {
    height: 53px; padding-left: 25px;
    background: linear-gradient(var(--panel-bar-top), var(--panel-bar-bottom));
    color: var(--white); font-size: 24px; font-weight: 400;
    display: flex; align-items: center;
  }
  .club-entry { position: absolute; left: 22px; width: 1120px; display: flex; gap: 19px; }
  .club-entry--first { top: 84px; }
  .club-entry--second { top: 283px; }
  .entry-photo {
    flex: none; width: 155px; height: 141px;
    background: linear-gradient(160deg, #4f9fe0 0%, #cfe6f2 45%, #e9e3d6 70%, #6d6250 100%);
    border: 1px solid #cfcfcf;
    box-shadow: 3px 3px 4px rgba(0,0,0,.35);
  }
  .entry-text {
    font-size: 13.5px; line-height: 22px; letter-spacing: 0.5px;
    color: var(--text); margin-top: -4px;
  }
  .entry-divider {
    position: absolute; left: 24px; top: 252px; width: 1127px; height: 1px; background: var(--rule);
  }
  .site-footer {
    position: absolute; left: 20px; top: 784px; width: 1167px; height: 83px;
    border-radius: 12px; border: 1px solid #e9dfc8;
    background: linear-gradient(var(--header-light), #d6c8a6 60%, #a8977a);
  }
  .social-links { position: absolute; left: 26px; top: 24px; display: flex; gap: 5px; }
  .social-link { width: 37px; height: 37px; border-radius: 5px; }
  .social-link--one { background: #3b5b9a; }
  .social-link--two { background: #5ec6ea; }
  .social-link--three { background: #e86a1c; }
  .copyright {
    position: absolute; left: 0; width: 100%; top: 37px; text-align: center;
    font-size: 13px; color: #2e2618;
  }
  .footer-brand {
    position: absolute; right: 28px; top: 22px;
    display: flex; align-items: center; gap: 8px;
    font-size: 34px; font-weight: 700; color: var(--brand);
  }
  .footer-brand .brand-dot { width: 20px; height: 20px; }
</style>
</head>
<body>
  <div class="nav-band"></div>

  <header class="site-header">
    <div class="header-scene" role="img" aria-label="Seaside coastline with beach, trees and a coastal road"></div>
    <div class="brand"><span class="brand-dot"></span>Velmora</div>
    <div class="phone-badge">
      <svg width="56" height="46" viewBox="0 0 56 46" aria-hidden="true">
        <path d="M4 14 Q28 0 52 14 L48 22 L38 18 L38 12 Q28 9 18 12 L18 18 L8 22 Z" fill="#fff"/>
        <path d="M14 24 L42 24 L48 42 L8 42 Z" fill="#fff"/>
        <circle cx="28" cy="33" r="5" fill="#a8792f"/>
      </svg>
    </div>
    <div class="phone-number">555-010-010</div>
  </header>

  <nav class="main-nav">
    <div class="nav-tab">About Us</div>
    <div class="nav-tab nav-tab--vip">VIP Club</div>
    <div class="nav-tab">Services</div>
    <div class="nav-tab">Packages &amp; Prices</div>
    <div class="nav-tab nav-tab--register">Registration</div>
    <div class="nav-tab">Contacts</div>
  </nav>

  <main class="content-panel">
    <h1 class="panel-title">VIP Club</h1>

    <section class="club-entry club-entry--first">
      <div class="entry-photo" role="img" aria-label="Couple in white robes relaxing on a seaside veranda"></div>
      <p class="entry-text">Lorem ipsum dolor sit amet consecutor. Lorem ipsum dolor sit amet consecutor. Lorem ipsum dolor sit amet consecutor. Lorem ipsum dolor sit amet consecutor. Lorem ipsum dolor sit amet consecutor. Lorem ipsum dolor sit amet consecutor. Lorem ipsum dolor sit amet consecutor. Lorem ipsum dolor sit amet consecutor. Lorem ipsum dolor sit amet consecutor. Lorem ipsum dolor sit amet consecutor. Lorem ipsum dolor sit amet consecutor. Lorem ipsum dolor sit amet consecutor. Lorem ipsum dolor sit amet consecutor. Lorem ipsum dolor sit amet consecutor. Lorem ipsum dolor sit amet consecutor. Lorem ipsum dolor sit amet consecutor. Lorem ipsum dolor sit amet consecutor. Lorem ipsum dolor sit amet consecutor. Lorem ipsum dolor sit amet consecutor. Lorem ipsum dolor sit amet consecutor. Lorem ipsum dolor sit amet consecutor. Lorem ipsum dolor sit amet consecutor. Lorem ipsum dolor sit amet consecutor. Lorem ipsum dolor sit amet consecutor.</p>
    </section>

    <div class="entry-divider"></div>

    <section class="club-entry club-entry--second">
      <div class="entry-photo" role="img" aria-label="Couple in white robes relaxing on a seaside veranda"></div>
      <p class="entry-text">Lorem ipsum dolor sit amet consecutor. Lorem ipsum dolor sit amet consecutor. Lorem ipsum dolor sit amet consecutor. Lorem ipsum dolor sit amet consecutor. Lorem ipsum dolor sit amet consecutor. Lorem ipsum dolor sit amet consecutor. Lorem ipsum dolor sit amet consecutor. Lorem ipsum dolor sit amet consecutor. Lorem ipsum dolor sit amet consecutor. Lorem ipsum dolor sit amet consecutor. Lorem ipsum dolor sit amet consecutor. Lorem ipsum dolor sit amet consecutor. Lorem ipsum dolor sit amet consecutor. Lorem ipsum dolor sit amet consecutor. Lorem ipsum dolor sit amet consecutor. Lorem ipsum dolor sit amet consecutor. Lorem ipsum dolor sit amet consecutor. Lorem ipsum dolor sit amet consecutor. Lorem ipsum dolor sit amet consecutor. Lorem ipsum dolor sit amet consecutor. Lorem ipsum dolor sit amet consecutor. Lorem ipsum dolor sit amet consecutor. Lorem ipsum dolor sit amet consecutor. Lorem ipsum dolor sit amet consecutor.</p>
    </section>
  </main>

  <footer class="site-footer">
    <div class="social-links">
      <span class="social-link social-link--one"></span>
      <span class="social-link social-link--two"></span>
      <span class="social-link social-link--three"></span>
    </div>
    <p class="copyright">Copyright ©2010 Velmora. All Rights Reserved</p>
    <div class="footer-brand"><span class="brand-dot"></span>Velmora</div>
  </footer>
</body>
</html>
```